1876 Basins & Spouts Business Card

I'm wanting to get a business card designed. Our business is 1876 Basins & Spouts
Details for the card:

1876 Basins & Spouts
Name: Harold Vesk
Email: harold@1876basinsandspouts.com.au
Website: www.1876basinsandspouts.com.au
Mobile: 0438 260 947
Phone: 02 7481 3926

Font of Basins & Spouts is called Snell Roundhand. Not sue what font logo text is.

I'm thinking two sided but it doesn't have to be.

```html
<!DOCTYPE html>
<html lang="en">
<head>
<meta charset="utf-8">
<title>1876 Basins &amp; Spouts Business Card</title>
<link href="https://fonts.googleapis.com/css2?family=Roboto:wght@300;400;700&display=swap" rel="stylesheet">
<style>
  :root {
    --backdrop: #3a3a3c;
    --card: #1c1c1e;
    --card-edge: #111113;
    --ink: #f2f2f2;
    --ink-soft: #bdbdbd;
    --rule: #8a8a8a;
  }
  * { box-sizing: border-box; margin: 0; padding: 0; }
  html, body { width: 1200px; height: 840px; overflow: hidden; }
  body {
    background: var(--backdrop);
    font-family: 'Roboto', Arial, sans-serif;
    color: var(--ink);
    display: flex;
    align-items: center;
    justify-content: center;
    gap: 40px;
  }
  .card {
    width: 540px;
    height: 330px;
    background: var(--card);
    border: 1px solid var(--card-edge);
    box-shadow: 0 18px 40px rgba(0,0,0,0.45);
    position: relative;
  }
  /* Back side */
  .card--back {
    display: flex;
    flex-direction: column;
    align-items: center;
    justify-content: center;
    gap: 26px;
  }
  .brand {
    display: flex;
    align-items: center;
    gap: 12px;
    white-space: nowrap;
  }
  .brand__dot {
    width: 16px; height: 16px;
    border-radius: 50%;
    background: var(--ink-soft);
    flex: none;
  }
  .brand__name {
    font-weight: 400;
    color: var(--ink);
  }
  .card--back .brand__name { font-size: 28px; letter-spacing: 0.5px; }
  .card--back .website { font-size: 14px; color: var(--ink); letter-spacing: 0.3px; }

  /* Front side */
  .card--front {
    display: flex;
    align-items: center;
    padding: 0 30px;
  }
  .identity {
    width: 232px;
    flex: none;
    display: flex;
    flex-direction: column;
    gap: 6px;
  }
  .card--front .brand { gap: 10px; }
  .card--front .brand__name { font-size: 19px; }
  .card--front .brand__dot { width: 12px; height: 12px; }
  .tagline {
    font-size: 8px;
    font-weight: 300;
    color: var(--ink-soft);
    padding-left: 22px;
    white-space: nowrap;
  }
  .divider {
    width: 1px;
    height: 150px;
    flex: none;
    margin: 0 22px 0 10px;
    background: linear-gradient(to bottom, transparent, var(--rule) 30%, var(--ink) 50%, var(--rule) 70%, transparent);
  }
  .contact { white-space: nowrap; }
  .contact__name {
    font-size: 19px;
    font-weight: 700;
    margin-bottom: 10px;
  }
  .contact__list { list-style: none; }
  .contact__item {
    display: flex;
    align-items: center;
    gap: 8px;
    font-size: 12.5px;
    line-height: 20px;
    color: var(--ink);
  }
  .contact__item svg { width: 11px; height: 11px; flex: none; fill: var(--ink); }
</style>
</head>
<body>
  <section class="card card--back" aria-label="Card back">
    <div class="brand">
      <span class="brand__dot"></span>
      <span class="brand__name">1876 Basins &amp; Spouts</span>
    </div>
    <p class="website">www.1876basinsandspouts.com.au</p>
  </section>

  <section class="card card--front" aria-label="Card front">
    <div class="identity">
      <div class="brand">
        <span class="brand__dot"></span>
        <span class="brand__name">1876 Basins &amp; Spouts</span>
      </div>
      <p class="tagline">Pairing classic elegance with everyday function</p>
    </div>
    <div class="divider"></div>
    <div class="contact">
      <p class="contact__name">Harold Vesk</p>
      <ul class="contact__list">
        <li class="contact__item">
          <svg viewBox="0 0 12 12"><path d="M2.5 1l2 2.2-1 1.3c.7 1.5 1.7 2.5 3.1 3.2l1.2-1 2.2 2-1 1.8C5 10.3 1.6 7 1 2.2z"/></svg>
          02 7481 3926
        </li>
        <li class="contact__item">
          <svg viewBox="0 0 12 12"><path d="M3 0h6v12H3zM4 1v9h4V1z"/></svg>
          0438 260 947
        </li>
        <li class="contact__item">
          <svg viewBox="0 0 12 12"><path d="M0 2h12v8H0zM1 3v.4l5 3.2 5-3.2V3zM1 4.6V9h10V4.6L6 7.8z"/></svg>
          harold@1876basinsandspouts.com.au
        </li>
        <li class="contact__item">
          <svg viewBox="0 0 12 12"><circle cx="6" cy="6" r="5.5"/></svg>
          www.1876basinsandspouts.com.au
        </li>
      </ul>
    </div>
  </section>
</body>
</html>
```